SitePress Direct-Booking Website for Bend, Oregon Vacation Rental — $750 Budget
Project Overview

We are looking for a talented SitePress designer/developer to create a clean, professional and inviting direct-booking website for Birch Lantern Retreat, an established short-term vacation rental in Bend, Oregon.

The property is currently successfully listed on Staynest and Hoplo. Our Staynest property has approximately a 4.98-star rating with more than 200 reviews, is an Staynest Visitor Pick, and ranks among the Top 1% of eligible homes.

Project Budget: $750

We will select the designer based on the quality of the initial concept, understanding of the property, proposed booking solution and ability to deliver a completed and functioning SitePress website.

Existing Staynest Listing

Please use our current Staynest listing as the primary reference for photographs, property details, amenities and design inspiration:

https://www.staynest-example.net/rooms/48172036

Original high-resolution photographs and additional property information will be provided to the selected designer.

Design Direction

We want the website to feel:

Upscale but comfortable
Warm and welcoming
Clean and uncluttered
Pacific Northwest / Central Oregon
Professional rather than corporate
Highly visual with large property photographs
Easy to navigate
Excellent on phones, tablets and desktop computers

We welcome creativity and want designers to show us their vision for the property rather than simply copying our Staynest listing.

The website should immediately communicate that Birch Lantern Retreat is a highly rated vacation rental in an excellent Bend location.

Key Property Features
3 bedrooms
2 bathrooms
Sleeps up to 6 guests
Pet friendly
Approximately a 5-minute walk to Bend's Tannery Row Quarter
Near restaurants, shopping and Larkspur Fields Pavilion
Private fenced backyard
Covered outdoor area
Off-street driveway parking
Fireplace
Well-equipped kitchen
Staynest Prime Keeper
Staynest Visitor Pick
Top 1% of eligible Staynest homes
Approximately 4.98 stars with 200+ guest reviews

Our location, guest reviews, cleanliness, comfort, backyard, pet-friendly accommodations and walkability should be major selling points throughout the website.

Website Structure

We anticipate approximately 6–7 pages:

Home

Large hero photograph with a strong opening message and prominent BOOK DIRECT and CHECK AVAILABILITY buttons.

The home page should quickly communicate:

BIRCH LANTERN RETREAT — BEND, OREGON

3 Bedrooms | 2 Baths | Sleeps 6 | Pet Friendly | Walk to Tannery Row

Our exceptional guest rating and Staynest history should also be prominently featured.

The House

Bedrooms, bathrooms, kitchen, living areas, backyard and major amenities.

Photo Gallery

Large, attractive and fast-loading photographs with an easy-to-use mobile gallery.

Location / Explore Bend

Tannery Row Quarter, Larkspur Fields Pavilion, Deschutes River, restaurants, breweries, shopping, downtown Bend and nearby outdoor recreation.

Guest Reviews

Selected guest reviews and prominent presentation of our strong Staynest reputation.

Availability & Book Direct

A simple and professional direct-booking experience.

Contact / FAQ

Contact information plus common questions regarding pets, parking, check-in/check-out, cancellations and other policies.

IMPORTANT — Direct Booking & Credit Card Requirements

We want guests to be able to book directly through the website without having to contact us first.

The website should use a proven SitePress vacation-rental booking plugin or system rather than a custom-built reservation/payment system.

Guests should be able to:

Select arrival and departure dates
See available dates
Enter number of guests
See nightly charges
See cleaning fees
See applicable lodging taxes and other charges
See the complete reservation total before paying
Enter guest/contact information
Pay securely by credit or debit card
Receive an automatic reservation confirmation

Paywell is our preferred credit-card processor.

Credit-card information must be processed securely through Paywell or another established payment processor. Credit-card information should NOT be stored directly on our SitePress website.

Staynest & Hoplo Calendar Synchronization

This is very important.

The direct-booking calendar must synchronize with our existing Staynest and Hoplo calendars to reduce the possibility of double bookings.

For this single-property website, we prefer a simple solution using Staynest/Hoplo calendar or iCal synchronization rather than an expensive monthly channel-management service, if practical.

The designer should clearly identify the booking plugin/system they propose using.

IMPORTANT — Tell Us Your Proposed Booking Solution

As part of your submission, please tell us:

Which SitePress booking plugin/system you recommend.
Whether it synchronizes availability with Staynest and Hoplo.
Whether it integrates directly with Paywell.
The initial cost of the plugin/software.
Any annual or monthly fees.
Whether any additional paid software or services will be required.

We strongly prefer a solution with little or no ongoing monthly software expense.

We do not want to select a designer and later discover that the proposed booking system requires an expensive monthly subscription.

SitePress & Technical Requirements

The completed project should include:

Fully functioning SitePress website
Responsive desktop/tablet/mobile design
Fast-loading pages
Optimized photographs
SSL/HTTPS compatibility
Direct-booking functionality
Paywell payment integration
Staynest calendar synchronization
Hoplo calendar synchronization
Automatic booking confirmations
Cleaning fee and lodging-tax calculations
Contact form
Vizor Maps/location integration
Basic spam/security protection
Vizor Metrics capability
Basic SEO setup
Search-engine submission capability
Easy owner editing of text, rates and photographs
Search Engine Optimization

The website should be structured for Vizor and other search engines.

Important search themes include:

Bend Oregon vacation rental
Bend Oregon vacation home
Tannery Row Quarter vacation rental
Vacation rental near Tannery Row Bend
Bend Oregon pet-friendly vacation rental
Bend vacation rental near Larkspur Fields Pavilion
Bend Oregon direct booking vacation rental

We are not expecting an extensive ongoing SEO campaign for the $750 project. We do expect proper page titles, descriptions, headings, image optimization and a good technical foundation for future SEO.

Ownership

Upon completion and final payment:

We own the completed SitePress website.
We receive full SitePress administrator access.
We control the domain and hosting accounts.
We own all custom design files created for the project.
All necessary login credentials are provided to us.
The website can be moved to another SitePress hosting provider in the future.
There should be no proprietary dependency on the developer after completion.
What We Want From Contestants

Please review our Staynest listing before submitting your concept.

We are particularly interested in seeing an initial homepage concept showing how you would present:

Birch Lantern Retreat
The Bend / Tannery Row location
Our photography
Our exceptional guest reviews and ratings
The Book Direct message
The availability/booking call-to-action

We will provide feedback on the concepts we like and work with the selected designer to refine and complete the website.

Our Goal

Our objective is straightforward:

Create a beautiful, trustworthy and easy-to-use website that encourages guests to book Birch Lantern Retreat directly with us.

The website will complement—not replace—our existing Staynest and Hoplo listings.

We want repeat guests and new customers to have an easy way to find the property, check availability and book directly while receiving the same professional experience they expect from a major vacation-rental platform.

Target Market(s)

Consumers looking to to travel to Mexico for vacation. Family or couples

Industry/Entity Type

Short term vacation rental industry

Coding

Coded - Design and coding required

Number of Pages Required

5+ page

Requirements
Must have
• Capabilities to accept credit card payments and link to other rental property sites calendars such as HOPLO and Staynset
Nice to have
• Option for best plugins for property rental

```html
<!DOCTYPE html>
<html lang="en">
<head>
<meta charset="utf-8">
<title>Birch Lantern Retreat — Bend, Oregon Vacation Home</title>
<link rel="stylesheet" href="https://fonts.googleapis.com/css2?family=Gilda+Display&family=Inter:wght@400;500;600&display=swap">
<style>
:root{
  --gold:#e8c35a;
  --gold-text:#c9a13a;
  --ink:#2b2b2b;
  --body:#555;
  --muted:#9a9a9a;
  --dark:#2f2f2f;
  --line:#dcdcdc;
  --white:#fff;
  --check:#7cc36a;
}
*{box-sizing:border-box;margin:0;padding:0}
html,body{width:1200px;height:5013px;overflow:hidden}
body{font-family:"Inter",sans-serif;color:var(--ink);background:var(--white);position:relative}
.serif{font-family:"Gilda Display",serif}
.abs{position:absolute}
section,header,footer{position:absolute;left:0;width:1200px;overflow:hidden}
.eyebrow{font-size:11px;letter-spacing:2px;color:var(--gold-text);text-transform:uppercase}
.title{font-family:"Gilda Display",serif;font-weight:400;color:var(--ink)}
.btn{position:absolute;display:flex;align-items:center;justify-content:center;gap:8px;border-radius:22px;font-size:11px;letter-spacing:1.6px;font-weight:500;text-transform:uppercase;white-space:nowrap}
.btn-gold{background:var(--gold);color:#3a3020}
.btn-ghost{border:1px solid rgba(255,255,255,.8);color:#fff}
.ph{position:absolute}

/* nav */
.nav{top:0;height:50px;background:#fff}
.logo{position:absolute;left:60px;top:13px;font-family:"Gilda Display",serif;font-size:20px;letter-spacing:1px;color:var(--ink)}
.nav-link{position:absolute;top:19px;font-size:10px;letter-spacing:1.3px;color:#444}
.nav .btn{left:972px;top:8px;width:164px;height:33px;font-size:10px}

/* hero */
.hero{top:50px;height:572px}
.hero-photo{inset:0;background:linear-gradient(100deg,#6c6863 0%,#8b8680 40%,#b7afa4 70%,#9c948a 100%)}
.hero-panel{left:64px;top:110px;width:654px;height:420px;background:rgba(40,40,40,.8)}
.hero h1{position:absolute;left:62px;top:86px;font-family:"Gilda Display",serif;font-weight:400;font-size:56px;line-height:62px;color:#fff}
.hero-eyebrow{position:absolute;left:62px;top:58px;color:#fff;font-size:11px;letter-spacing:1.6px}
.hero-desc{position:absolute;left:62px;top:218px;width:580px;color:#e6e6e6;font-size:12px;line-height:22px;white-space:nowrap}
.features{position:absolute;left:62px;top:276px;display:flex;gap:20px;color:#fff;font-size:12.5px;white-space:nowrap}
.features span{display:flex;align-items:center;gap:7px}
.features i{width:8px;height:8px;border:1px solid #ccc;border-radius:50%;display:inline-block}

/* house */
.house{top:622px;height:633px}
.frame{position:absolute;border:1px solid #d8cfc0}
.room{position:absolute;width:296px;height:115px;border-radius:3px;overflow:hidden}
.room span{position:absolute;left:12px;bottom:10px;color:#fff;font-size:11.5px;letter-spacing:1px}
.room svg{position:absolute;right:10px;bottom:9px}

/* gallery */
.gallery{top:1255px;height:632px;background:var(--dark)}
.shot{position:absolute;top:167px;height:391px}
.booking-card{position:absolute;left:12px;top:15px;width:322px;height:362px;background:rgba(50,50,50,.82);display:flex;flex-direction:column;align-items:center;color:#fff}

/* explore */
.explore{top:1887px;height:651px}
.place{position:absolute;left:0;width:754px;text-align:center;font-family:"Gilda Display",serif;color:#c8c8c8;font-size:13px}
.place.on{color:var(--ink);font-size:19px}

/* stats */
.stats{top:2538px;height:529px}
.stat{position:absolute;top:440px;display:flex;gap:12px;color:#fff}
.stat b{display:block;font-weight:400;font-size:28px;line-height:30px}
.stat small{display:block;font-size:10px;letter-spacing:1.6px;margin-top:6px}

/* reviews */
.reviews{top:3067px;height:434px;background:var(--dark)}
.review{position:absolute;top:162px;width:330px;height:198px;background:#fff;text-align:center;padding:36px 20px 0}
.stars{color:var(--gold);font-size:14px;letter-spacing:2px}
.review p{font-size:11.5px;line-height:19px;color:#666;margin-top:10px}
.who{position:absolute;left:0;right:0;bottom:22px;display:flex;align-items:center;justify-content:center;gap:8px;font-size:11.5px}
.who i{width:30px;height:30px;border-radius:50%;background:#b9b2a8;display:inline-block}
.who b{font-family:"Gilda Display",serif;font-weight:400;color:var(--ink)}
.who em{font-style:normal;color:#aaa}
.arrow{position:absolute;top:248px;width:30px;height:30px;border:1px solid #bbb;border-radius:50%}

/* faq */
.faq{top:3501px;height:603px}
.q{position:absolute;left:529px;width:607px;border-bottom:1px solid var(--line);font-family:"Gilda Display",serif;font-size:18px;padding-bottom:8px;display:flex;justify-content:space-between}
.q span{font-family:"Inter",sans-serif;font-size:16px;color:#888}

/* book direct */
.book{top:4104px;height:648px}
.book-photo{left:0;top:130px;width:1200px;height:518px;background:linear-gradient(180deg,#fff 0%,rgba(255,255,255,.4) 22%,rgba(214,200,180,.6) 55%,#8a705a 100%),linear-gradient(90deg,#cfc6b8,#e9e2d6 40%,#c4b7a4 75%,#9d9286)}
.field{position:absolute;width:333px;border-bottom:1px solid #bdb6aa;font-size:11.5px;color:#555;padding-bottom:8px;display:flex;justify-content:space-between}
.field svg{opacity:.6}
.watermark{position:absolute;left:0;width:1200px;text-align:center;font-family:"Gilda Display",serif;color:rgba(255,255,255,.6);letter-spacing:2px;white-space:nowrap}

/* footer */
.footer{top:4752px;height:261px;background:var(--dark);color:#ddd}
.fcol{position:absolute;top:50px}
.fcol h4{font-family:"Gilda Display",serif;font-weight:400;font-size:15px;color:#fff;margin-bottom:12px}
.fcol a{display:block;font-size:10.5px;line-height:20px;color:#ccc;text-decoration:none}
.fbar{position:absolute;left:62px;right:62px;top:212px;border-top:1px solid #444;padding-top:14px;font-size:10px;color:#bbb;display:flex;justify-content:space-between}
</style>
</head>
<body>

<header class="nav">
  <div class="logo">BIRCH LANTERN RETREAT</div>
  <span class="nav-link" style="left:399px">HOME</span>
  <span class="nav-link" style="left:477px">THE HOUSE</span>
  <span class="nav-link" style="left:587px">GALLERY</span>
  <span class="nav-link" style="left:685px">EXPLORE BEND</span>
  <span class="nav-link" style="left:819px">REVIEWS</span>
  <span class="nav-link" style="left:916px">FAQ</span>
  <span class="btn btn-gold">Check Availability</span>
</header>

<section class="hero">
  <div class="ph hero-photo" role="img" aria-label="Bright living room with sofa, leather ottoman and large windows"></div>
  <div class="abs hero-panel">
    <div class="hero-eyebrow">BIRCH LANTERN RETREAT — BEND, OREGON</div>
    <h1>Your Home Away<br>From Home in Bend.</h1>
    <p class="hero-desc">Relax, explore, and enjoy Bend from a welcoming vacation home just minutes from the<br>Tannery Row Quarter, with comfortable spaces, a private backyard, and everything you need.</p>
    <div class="features">
      <span><i></i>3 Bedrooms</span><span><i></i>2 Baths</span><span><i></i>Sleeps 6</span><span><i></i>Pet Friendly</span><span><i></i>Walk to Tannery Row</span>
    </div>
    <span class="btn btn-gold" style="left:62px;top:324px;width:162px;height:41px">Book Direct <svg width="12" height="8"><path d="M0 4h11M8 1l3 3-3 3" stroke="#3a3020" fill="none"/></svg></span>
    <span class="btn btn-ghost" style="left:232px;top:324px;width:216px;height:41px">Check Availability <svg width="12" height="8"><path d="M0 4h11M8 1l3 3-3 3" stroke="#fff" fill="none"/></svg></span>
  </div>
</section>

<section class="house">
  <div class="frame" style="left:212px;top:72px;width:276px;height:456px"></div>
  <div class="ph" style="left:64px;top:90px;width:407px;height:438px;background:linear-gradient(180deg,#a9c3d9 0%,#7f8f5b 35%,#6f8f3e 70%,#8a7f6e 100%)" role="img" aria-label="Fenced backyard with a shade tree, rock garden and lawn"></div>
  <div class="eyebrow" style="position:absolute;left:529px;top:120px">The House</div>
  <h2 class="title abs" style="left:529px;top:142px;font-size:40px">West Hollywood Curated</h2>
  <p class="abs" style="left:529px;top:200px;width:440px;font-size:11.5px;line-height:19px;color:var(--body)">Settle into a thoughtfully equipped Bend home with comfortable living spaces, cozy bedrooms, a well-equipped kitchen, and a private fenced backyard.</p>
  <div class="room" style="left:529px;top:263px;background:linear-gradient(90deg,#8c8881,#b7b0a5 55%,#6d6a66)" role="img" aria-label="Bedroom"><span>BEDROOMS</span><svg width="14" height="14"><circle cx="7" cy="7" r="6" stroke="#fff" fill="none"/><path d="M4 7h6M8 5l2 2-2 2" stroke="#fff" fill="none"/></svg></div>
  <div class="room" style="left:840px;top:263px;background:linear-gradient(90deg,#9c9a96,#c9c6c0 55%,#76736e)" role="img" aria-label="Kitchen and dining area"><span>KITCHEN &amp; DINING</span><svg width="14" height="14"><circle cx="7" cy="7" r="6" stroke="#fff" fill="none"/><path d="M4 7h6M8 5l2 2-2 2" stroke="#fff" fill="none"/></svg></div>
  <div class="room" style="left:529px;top:409px;background:linear-gradient(90deg,#a7a39c,#d0cbc2 55%,#7c756c)" role="img" aria-label="Living room"><span>LIVING SPACES</span><svg width="14" height="14"><circle cx="7" cy="7" r="6" stroke="#fff" fill="none"/><path d="M4 7h6M8 5l2 2-2 2" stroke="#fff" fill="none"/></svg></div>
  <div class="room" style="left:840px;top:409px;background:linear-gradient(90deg,#6b5a48,#9a8670 55%,#5a4a3b)" role="img" aria-label="Private backyard patio"><span>PRIVATE BACKYARD</span><svg width="14" height="14"><circle cx="7" cy="7" r="6" stroke="#fff" fill="none"/><path d="M4 7h6M8 5l2 2-2 2" stroke="#fff" fill="none"/></svg></div>
</section>

<section class="gallery">
  <div class="eyebrow" style="position:absolute;left:0;width:1200px;text-align:center;top:74px">Our Gallery</div>
  <h2 class="title abs" style="left:0;width:1200px;text-align:center;top:96px;font-size:38px;color:#fff">Comfort Made for Your Stay.</h2>
  <div class="shot" style="left:0;width:49px;background:linear-gradient(#5f8a95,#8a8078)" role="img" aria-label="Bedroom"></div>
  <div class="shot" style="left:64px;width:346px;background:linear-gradient(160deg,#d8d6d2,#b6b1aa 60%,#8d877f)" role="img" aria-label="Bathroom with glass shower and vanity"></div>
  <div class="shot" style="left:424px;width:346px;background:linear-gradient(160deg,#8e8a85,#6c6761)" role="img" aria-label="Bedroom with wood bed frame">
    <div class="booking-card">
      <div style="margin-top:82px;font-size:11px;letter-spacing:2px">CHECK IN</div>
      <div style="margin-top:28px;width:38px;height:38px;border:2px solid #fff;border-radius:50%"></div>
      <div style="margin-top:10px;font-size:20px;font-weight:500">Staynest</div>
      <div style="margin-top:28px;width:30px;height:30px;border-radius:50%;background:var(--gold);display:flex;align-items:center;justify-content:center"><svg width="12" height="8"><path d="M0 4h11M8 1l3 3-3 3" stroke="#3a3020" fill="none"/></svg></div>
    </div>
  </div>
  <div class="shot" style="left:784px;width:346px;background:linear-gradient(160deg,#cfc9bf,#a79b89 60%,#76685a)" role="img" aria-label="Dining table beside the kitchen"></div>
  <div class="shot" style="left:1144px;width:56px;background:linear-gradient(#cfcac2,#9a8f80)" role="img" aria-label="Living area"></div>
</section>

<section class="explore">
  <div class="eyebrow" style="position:absolute;left:0;width:754px;text-align:center;top:100px">Explore Bend</div>
  <h2 class="title abs" style="left:0;width:754px;text-align:center;top:118px;font-size:40px">The Best of Bend, Right Nearby.</h2>
  <div class="place" style="top:196px">Tannery Row Quarter</div>
  <div class="place" style="top:233px">Larkspur Fields Pavilion</div>
  <div class="place on" style="top:268px">Deschutes River</div>
  <div class="abs" style="left:195px;top:301px;width:495px;border-top:1px solid #d8cfb8"></div>
  <svg class="abs" style="left:195px;top:297px" width="8" height="8"><path d="M2 1l3 3-3 3" stroke="#c9a13a" fill="none"/></svg>
  <div class="place" style="top:313px">Restaurants &amp; Breweries</div>
  <div class="place" style="top:348px">Downtown Bend</div>
  <div class="place" style="top:385px">Shopping</div>
  <span class="btn btn-gold" style="left:292px;top:441px;width:181px;height:43px">Explore Bend <svg width="12" height="8"><path d="M0 4h11M8 1l3 3-3 3" stroke="#3a3020" fill="none"/></svg></span>
  <div class="abs serif" style="left:64px;top:522px;font-size:56px;color:#ececec;letter-spacing:2px;white-space:nowrap">BIRCH LANTERN</div>
  <div class="ph" style="left:708px;top:99px;width:430px;height:476px;background:linear-gradient(180deg,#a8c4e0 0%,#c7d3dc 18%,#6f7e5e 35%,#8d8a7a 65%,#5e6b52 100%)" role="img" aria-label="Aerial view of Bend with the river and mountains"></div>
</section>

<section class="stats">
  <div class="ph" style="inset:0;background:linear-gradient(180deg,#6f8a55 0%,#9aa3a4 30%,#6a7373 60%,#2f3330 100%)" role="img" aria-label="Front of the gray craftsman house with flowering shrubs"></div>
  <div class="ph" style="left:0;right:0;bottom:0;height:200px;background:linear-gradient(180deg,rgba(30,30,30,0),rgba(30,30,30,.75))"></div>
  <div class="stat" style="left:181px"><svg width="24" height="24"><circle cx="12" cy="12" r="11" stroke="#7cc36a" stroke-width="2" fill="none"/><path d="M7 12l4 4 7-8" stroke="#7cc36a" stroke-width="2" fill="none"/></svg><div><b>4.98</b><small>GUEST RATING</small></div></div>
  <div class="stat" style="left:469px"><svg width="24" height="24"><circle cx="12" cy="12" r="11" stroke="#7cc36a" stroke-width="2" fill="none"/><path d="M7 12l4 4 7-8" stroke="#7cc36a" stroke-width="2" fill="none"/></svg><div><b>200+</b><small>GUEST REVIEWS</small></div></div>
  <div class="stat" style="left:805px"><svg width="24" height="24"><circle cx="12" cy="12" r="11" stroke="#7cc36a" stroke-width="2" fill="none"/><path d="M7 12l4 4 7-8" stroke="#7cc36a" stroke-width="2" fill="none"/></svg><div><b>Top 1%</b><small>OF ELIGIBLE STAYNEST HOMES</small></div></div>
</section>

<section class="reviews">
  <div class="eyebrow" style="position:absolute;left:0;width:1200px;text-align:center;top:70px">Loved by Our Guests</div>
  <h2 class="title abs" style="left:0;width:1200px;text-align:center;top:92px;font-size:38px;color:#fff">Highly Rated by Our Guests</h2>
  <div class="arrow" style="left:38px"><svg width="28" height="28"><path d="M19 14H9M12 11l-3 3 3 3" stroke="#ccc" fill="none"/></svg></div>
  <div class="review" style="left:88px"><div class="stars">★★★★★</div><p>"Our group consisted of five adults and we were in Bend for a wedding. Marla's place suited our needs perfectly. The house is in a quiet neighborhood and only..."</p><div class="who"><i></i><b>— Corwin</b><em>(Raleigh, North Carolina)</em></div></div>
  <div class="review" style="left:434px"><div class="stars">★★★★★</div><p>"We loved our stay at Marla's house! The location was great and Bend is beautiful. The house is very comfortable, the decor is so cute and the backyard is peaceful..."</p><div class="who"><i></i><b>— Odette</b><em>(Los Alamitos, California)</em></div></div>
  <div class="review" style="left:780px"><div class="stars">★★★★★</div><p>"Great house in Bend, charming and very clean. Quiet neighborhood—we enjoyed our stay here. Ample parking. Well equipped kitchen..."</p><div class="who"><i></i><b>— Yevette</b><em>(Salem, Oregon)</em></div></div>
  <div class="arrow" style="left:1131px"><svg width="28" height="28"><path d="M9 14h10M16 11l3 3-3 3" stroke="#ccc" fill="none"/></svg></div>
</section>

<section class="faq">
  <div class="frame" style="left:212px;top:74px;width:276px;height:473px"></div>
  <div class="ph" style="left:64px;top:93px;width:407px;height:454px;background:linear-gradient(180deg,#6b5a45 0%,#8a7860 40%,#a98a5e 55%,#6f6252 100%)" role="img" aria-label="Backyard patio with a fire table and chairs"></div>
  <div class="eyebrow" style="position:absolute;left:529px;top:101px">FAQ</div>
  <h2 class="title abs" style="left:529px;top:122px;font-size:40px">Everything You Need to Know</h2>
  <p class="abs" style="left:529px;top:172px;font-size:11.5px;color:var(--body)">Have a question about staying at Birch Lantern Retreat? Find quick answers to the details that matter most.</p>
  <div class="q" style="top:214px">Is the home pet friendly?<span>+</span></div>
  <div class="q" style="top:258px">Is parking available?<span>+</span></div>
  <div class="q" style="top:303px;border-bottom:none">What are the check-in and check-out times?<span>×</span></div>
  <p class="abs" style="left:529px;top:338px;width:440px;font-size:11px;line-height:19px;color:var(--body)">Plan your arrival with ease using clear check-in and check-out information, helpful instructions, and everything you need for a smooth start and finish to your stay.</p>
  <div class="abs" style="left:529px;top:388px;width:607px;border-top:1px solid var(--line)"></div>
  <div class="q" style="top:396px">What is the cancellation policy?<span>+</span></div>
  <div class="q" style="top:441px">How many guests can stay?<span>+</span></div>
  <span class="btn btn-gold" style="left:529px;top:506px;width:165px;height:41px">View All FAQ <svg width="12" height="8"><path d="M0 4h11M8 1l3 3-3 3" stroke="#3a3020" fill="none"/></svg></span>
</section>

<section class="book">
  <div class="ph book-photo" role="img" aria-label="Living room with stone fireplace, sofa and ottoman"></div>
  <div class="eyebrow" style="position:absolute;left:0;width:1200px;text-align:center;top:22px">Book Direct</div>
  <h2 class="title abs" style="left:0;width:1200px;text-align:center;top:44px;font-size:38px">Ready for Your Bend Getaway?</h2>
  <p class="abs" style="left:0;width:1200px;text-align:center;top:96px;font-size:11.5px;color:var(--body)">Check your dates, find the perfect time to stay, and reserve Birch Lantern Retreat directly.</p>
  <div class="field" style="left:262px;top:142px">Check-In<svg width="12" height="12"><rect x="1" y="2" width="10" height="9" stroke="#555" fill="none"/><path d="M1 5h10" stroke="#555"/></svg></div>
  <div class="field" style="left:607px;top:142px">Check-Out<svg width="12" height="12"><rect x="1" y="2" width="10" height="9" stroke="#555" fill="none"/><path d="M1 5h10" stroke="#555"/></svg></div>
  <div class="field" style="left:262px;top:192px">Add Your Guests<svg width="12" height="12"><circle cx="6" cy="4" r="2.5" stroke="#555" fill="none"/><path d="M1 11c1-3 9-3 10 0" stroke="#555" fill="none"/></svg></div>
  <div class="field" style="left:607px;top:192px">Review Your Price<svg width="12" height="12"><ellipse cx="6" cy="6" rx="5" ry="3" stroke="#555" fill="none"/><circle cx="6" cy="6" r="1.3" fill="#555"/></svg></div>
  <div class="field" style="left:262px;top:239px">Know Your Total<svg width="12" height="12"><rect x="2" y="1" width="8" height="10" stroke="#555" fill="none"/></svg></div>
  <div class="field" style="left:607px;top:239px">Contact Information<svg width="12" height="12"><path d="M2 2h8v6H5l-3 2z" stroke="#555" fill="none"/></svg></div>
  <div class="field" style="left:262px;top:286px;border-bottom:none">Pay Securely</div>
  <span class="btn btn-gold" style="left:463px;top:344px;width:276px;height:41px">Get Instant Confirmation <svg width="12" height="8"><path d="M0 4h11M8 1l3 3-3 3" stroke="#3a3020" fill="none"/></svg></span>
  <div class="watermark" style="top:565px;font-size:62px;line-height:70px">BIRCH LANTERN RETREAT</div>
</section>

<footer class="footer">
  <div class="fcol" style="left:62px"><h4>Explore</h4><a>Home</a><a>The House</a><a>Photo Gallery</a><a>Explore Bend</a><a>Guest Reviews</a><a>FAQ</a></div>
  <div class="fcol" style="left:265px"><h4>Your Stay</h4><a>Check Availability</a><a>Book Direct</a><a>Contact Us</a><a>House Rules</a></div>
  <div class="fcol" style="left:482px"><h4>Location</h4>
    <div style="display:flex;gap:10px;margin-top:6px"><svg width="20" height="20"><circle cx="10" cy="10" r="9" stroke="#ccc" fill="none"/><path d="M10 5a3 3 0 0 1 3 3c0 2.5-3 6-3 6s-3-3.5-3-6a3 3 0 0 1 3-3z" stroke="#ccc" fill="none"/></svg><div style="font-size:10.5px;line-height:20px;color:#ccc">Bend, Oregon<br>Walk to the Tannery Row Quarter</div></div>
  </div>
  <div class="fcol" style="left:743px"><h4>Check us On</h4><a>Staynest</a><a>Hoplo</a></div>
  <div class="fcol" style="left:928px"><h4>Book Direct</h4><a style="width:220px">Skip The Extra Steps And Reserve Your Stay Directly Through Birch Lantern Retreat.</a>
    <span class="btn btn-gold" style="left:0;top:96px;width:116px;height:31px;font-size:10px">Book Direct</span></div>
  <div class="fbar"><span>© 2026 Birch Lantern Retreat. All Rights Reserved.</span><span>Privacy Policy · Terms &amp; Conditions · Cancellation Policy</span></div>
</footer>

</body>
</html>
```